Website visual upgrade

I am seeking expressions of interest for the updating the visuals of my website www.kelvastaffing.net
I am basically seeking a simple,bold and visually strong graphic makeover.using existing or shortly to be modified text.

```html
<!DOCTYPE html>
<html lang="en">
<head>
<meta charset="utf-8">
<title>Kelva Staffing</title>
<link rel="stylesheet" href="https://fonts.googleapis.com/css2?family=Source+Sans+3:wght@300;400;600&display=swap">
<style>
:root{
  --red:#c8102e;
  --red-light:#e23a55;
  --ink:#222024;
  --text:#555;
  --muted:#777;
  --line:#cfcfcf;
  --band:#6e6e6e;
  --white:#fff;
}
*{box-sizing:border-box;margin:0;padding:0}
html,body{width:950px;height:1200px;overflow:hidden;background:var(--white)}
body{position:relative;font-family:"Source Sans 3",sans-serif;color:var(--text)}
.topline{position:absolute;left:0;top:0;width:950px;height:3px;background:var(--ink)}
.brand{position:absolute;left:92px;top:26px;display:flex;align-items:center;gap:10px}
.brand-dot{width:26px;height:26px;border-radius:50%;background:var(--ink)}
.brand-name{font-size:26px;font-weight:600;color:var(--red);letter-spacing:.5px}
.search{position:absolute;left:684px;top:30px;width:174px;height:28px;border:1px solid #d5d5d5;border-radius:4px;box-shadow:0 1px 2px rgba(0,0,0,.08);font-size:9px;color:#666;padding:8px 12px}
.search svg{position:absolute;right:10px;top:6px}
.nav{position:absolute;left:0;top:80px;width:950px;height:45px;background:var(--red);display:flex;padding-left:79px}
.nav a{display:block;height:45px;line-height:45px;color:var(--white);font-size:12.5px;text-decoration:none;padding:0 12px}
.nav a.active{background:var(--ink);padding:0 18px}
.hero{position:absolute;left:0;top:125px;width:950px;height:390px;background:linear-gradient(90deg,#d9d4d0 0%,#ece9e6 35%,#e3d2c6 65%,#d8d8da 100%)}
.hero-caption{position:absolute;left:0;top:307px;width:950px;height:83px;background:rgba(90,90,90,.78);color:var(--white);font-size:12.8px;line-height:18px;text-align:center;padding-top:24px}
.hero-caption svg{position:absolute;top:36px}
.welcome{position:absolute;left:0;top:530px;width:950px;text-align:center}
.welcome h1{font-size:28px;font-weight:300;color:#333}
.welcome p{font-size:13px;line-height:18px;color:#444;margin-top:8px}
.feature{position:absolute;top:634px;width:260px;text-align:center}
.frame{position:relative;width:153px;height:133px;margin:0 auto}
.frame i{position:absolute;background:var(--line)}
.frame .h{height:1px;left:0;right:0}
.frame .v{width:1px;top:0;bottom:0}
.icon-box{position:absolute;left:21px;top:24px;width:105px;height:84px;display:flex;align-items:center;justify-content:center}
.icon-box.red{background:linear-gradient(180deg,var(--red-light),var(--red))}
.feature h2{font-size:17px;font-weight:300;color:#333;margin-top:10px}
.feature p{font-size:13px;font-weight:300;line-height:19px;color:var(--muted);margin-top:6px}
.btn{display:inline-block;margin-top:12px;width:78px;height:26px;line-height:26px;background:var(--red);color:var(--white);font-size:10.5px;border-radius:2px;box-shadow:0 2px 2px rgba(0,0,0,.25)}
.support{position:absolute;left:70px;top:918px;width:810px;height:86px;border-top:2px solid #bbb;border-bottom:1px solid #ddd;background:linear-gradient(#f6f6f6,#fff)}
.support h3{position:absolute;left:164px;top:36px;font-size:22px;font-weight:400;color:var(--red)}
.badge{position:absolute;top:29px;height:40px}
.quick{position:absolute;left:129px;top:1036px}
.footer-title{font-size:13.5px;color:#333}
.quick ul{list-style:none;position:absolute;top:28px;font-size:10.5px;line-height:18px;color:#444;white-space:nowrap}
.follow{position:absolute;left:431px;top:1036px}
.social{display:flex;gap:6px;margin-top:12px}
.social span{width:19px;height:19px;border:1px solid #bbb;border-radius:3px;background:#f2f2f2;display:flex;align-items:center;justify-content:center}
.social b{width:9px;height:9px;background:#555;border-radius:1px}
.newsletter{position:absolute;left:622px;top:1036px}
.email{position:absolute;left:-4px;top:25px;width:128px;height:26px;border:1px solid #ddd;border-radius:4px;font-size:9px;color:#333;padding:7px 8px;white-space:nowrap}
.subscribe{position:absolute;left:132px;top:25px;width:84px;height:26px;background:linear-gradient(#fafafa,#e6e6e6);border-radius:4px;font-size:12px;color:#222;text-align:center;line-height:26px}
.bottom{position:absolute;left:0;top:1145px;width:950px;height:55px;background:var(--ink);color:#999;font-size:10.5px;text-align:center;line-height:55px}
</style>
</head>
<body>
<div class="topline"></div>
<header>
  <div class="brand"><span class="brand-dot"></span><span class="brand-name">Kelva Staffing</span></div>
  <div class="search">Search
    <svg width="14" height="14" viewBox="0 0 14 14"><circle cx="6" cy="6" r="4.5" fill="none" stroke="#777" stroke-width="1.4"/><line x1="9.3" y1="9.3" x2="13" y2="13" stroke="#777" stroke-width="1.8"/></svg>
  </div>
</header>
<nav class="nav">
  <a class="active">Home</a><a>Who we are</a><a>Our Approach</a><a>What we do</a><a>Migration Assistance</a><a>Job Seeker</a><a>Useful Links</a><a>Support</a><a>Contact Us</a>
</nav>
<section class="hero" role="img" aria-label="Photo of a smiling young man in an office with blurred colleagues behind">
  <div class="hero-caption">
    <svg style="left:94px" width="12" height="20" viewBox="0 0 12 20"><polyline points="10,2 2,10 10,18" fill="none" stroke="#fff" stroke-width="2.2"/></svg>
    Sed ut perspiciatis unde omnis iste natus error sit voluptatem accusantium doloremque laudantium, totam rem aperiam,<br>eaque ipsa quae ab illo inventore veritatis et quasi architecto beatae vitae dicta sunt explicabo.
    <svg style="left:840px" width="12" height="20" viewBox="0 0 12 20"><polyline points="2,2 10,10 2,18" fill="none" stroke="#fff" stroke-width="2.2"/></svg>
  </div>
</section>
<section class="welcome">
  <h1>Welcome</h1>
  <p>Sed ut perspiciatis unde omnis iste natus error sit voluptatem accusantium doloremque laudantium, totam rem aperiam,<br>eaque ipsa quae ab illo inventore veritatis et quasi architecto beatae vitae dicta sunt explicabo.</p>
</section>

<div class="feature" style="left:82px">
  <div class="frame"><i class="h" style="top:12px"></i><i class="h" style="bottom:12px"></i><i class="v" style="left:12px"></i><i class="v" style="right:12px"></i>
    <div class="icon-box red"><svg width="46" height="52" viewBox="0 0 46 52" fill="none" stroke="#fff" stroke-width="1.6"><path d="M16 30c-4-3-6-7-6-11a13 13 0 0 1 26 0c0 4-2 8-6 11v6H16z"/><line x1="17" y1="40" x2="29" y2="40"/><line x1="18" y1="44" x2="28" y2="44"/><line x1="23" y1="1" x2="23" y2="4"/><line x1="5" y1="19" x2="1" y2="19"/><line x1="41" y1="19" x2="45" y2="19"/><line x1="9" y1="7" x2="6" y2="4"/><line x1="37" y1="7" x2="40" y2="4"/></svg></div>
  </div>
  <h2>WHO WE ARE</h2>
  <p>Lorem ipsum dolor sit amet, consectetur adipiscing elit. Vivamus eget elit eu velit vehicula feugiat.</p>
  <span class="btn">Read more</span>
</div>
<div class="feature" style="left:341px">
  <div class="frame"><i class="h" style="top:12px"></i><i class="h" style="bottom:12px"></i><i class="v" style="left:12px"></i><i class="v" style="right:12px"></i>
    <div class="icon-box"><svg width="72" height="64" viewBox="0 0 72 64" fill="#444"><circle cx="26" cy="38" r="17"/><circle cx="54" cy="20" r="12"/><circle cx="26" cy="38" r="6" fill="#fff"/><circle cx="54" cy="20" r="4" fill="#fff"/></svg></div>
  </div>
  <h2>WHAT WE DO</h2>
  <p>Lorem ipsum dolor sit amet, consectetur adipiscing elit. Vivamus eget elit eu velit vehicula feugiat.</p>
  <span class="btn">Read more</span>
</div>
<div class="feature" style="left:606px">
  <div class="frame"><i class="h" style="top:12px"></i><i class="h" style="bottom:12px"></i><i class="v" style="left:12px"></i><i class="v" style="right:12px"></i>
    <div class="icon-box"><svg width="70" height="66" viewBox="0 0 70 66"><circle cx="35" cy="33" r="33" fill="#555"/><circle cx="24" cy="30" r="9" fill="#888"/><circle cx="46" cy="30" r="9" fill="#888"/><rect x="13" y="40" width="22" height="20" rx="8" fill="#888"/><rect x="35" y="40" width="22" height="20" rx="8" fill="#888"/></svg></div>
  </div>
  <h2>JOB SEEKER</h2>
  <p>Lorem ipsum dolor sit amet, consectetur adipiscing elit. Vivamus eget elit eu velit vehicula feugiat.</p>
  <span class="btn">Read more</span>
</div>

<section class="support">
  <h3>WE PROUDLY SUPPORT</h3>
  <div class="badge" style="left:414px;width:96px;background:#f1eef4;border:1px solid #ddd"></div>
  <div class="badge" style="left:530px;width:37px;background:#111"></div>
</section>

<footer>
  <div class="quick">
    <div class="footer-title">Quick Links</div>
    <ul style="left:0"><li>Home</li><li>Who we are</li><li>Our Approach</li></ul>
    <ul style="left:88px"><li>What we do</li><li>Migration Assistance</li><li>Job Seeker</li></ul>
    <ul style="left:208px"><li>Useful Links</li><li>Support</li><li>Contact Us</li></ul>
  </div>
  <div class="follow">
    <div class="footer-title">Follow Us On</div>
    <div class="social">
      <span><svg width="13" height="9" viewBox="0 0 13 9" fill="none" stroke="#555"><rect x=".5" y=".5" width="12" height="8"/><polyline points=".5,.5 6.5,5 12.5,.5"/></svg></span>
      <span><b></b></span><span><b></b></span><span><b></b></span><span><b></b></span>
    </div>
  </div>
  <div class="newsletter">
    <div class="footer-title">NewsLetter</div>
    <div class="email">Enter your email id</div>
    <div class="subscribe">SUBSCRIBE</div>
  </div>
  <div class="bottom">© 2013.www.kelvastaffing.net &nbsp;|&nbsp; Terms and Conditions *</div>
</footer>
</body>
</html>
```